Corvane Business Cards

Front of business card will have logo, name, address, & telephone number. Back of card will have a list of services provided - Roads, Substation Pads, Temporary Pads, Site Pads, Land Leveling, Powerline Row Cleaning, Land Clearing, Gates, Fencing, Construction Entrances, Excavation, Trenching, Underground Utilities, Directional Boring, Pile Driving. We are a construction company that uses heavy equipment like bulldozers, motor graders/blades, dump trucks, backhoes, hydro axes, & skid loaders. We build roads, pads, & install electric utility lines & waterlines underground. This logo is new. The word "Construction" can be smaller as uploaded 2 example edited logos. We will be using this card design for many employees.
Target Market(s)
Industrial Electric Powerline, Wind Turbine, Solar Panel, & Water Utility companies.
Contact Information for Business Card
Name/Position - Dwayne Halster - Owner
Address: 4875 FM 309
Merkel, TX 79412
Phone number - (325) 482-5096

```html
<!DOCTYPE html>
<html lang="en">
<head>
<meta charset="utf-8">
<title>Corvane Business Cards</title>
<link rel="stylesheet" href="https://fonts.googleapis.com/css2?family=Arimo:wght@400;700&display=swap">
<style>
  :root {
    --backdrop: #5e5e5e;
    --maroon: #3a111a;
    --paper: #ffffff;
    --ink: #2e2e2e;
    --ink-soft: #444444;
    --rule: #8c5b63;
    --on-maroon: #ffffff;
  }
  * { margin: 0; padding: 0; box-sizing: border-box; }
  html, body {
    width: 1200px;
    height: 900px;
    overflow: hidden;
    background: var(--backdrop);
    font-family: "Arimo", Arial, sans-serif;
  }
  .canvas {
    position: relative;
    width: 1200px;
    height: 900px;
  }
  .card {
    position: absolute;
    top: 200px;
    width: 310px;
    height: 502px;
    box-shadow: 3px 4px 6px rgba(0, 0, 0, 0.35);
  }
  .card-front {
    left: 253px;
    background: var(--paper);
    border-radius: 62px 0 62px 0;
  }
  .card-back {
    left: 627px;
    background: var(--maroon);
    border-radius: 0 62px 0 62px;
    color: var(--on-maroon);
    text-align: center;
    font-size: 14.5px;
    line-height: 18.9px;
  }
  .brand {
    position: absolute;
    left: 40px;
    top: 112px;
    width: 230px;
    color: var(--maroon);
    font-weight: 700;
    text-align: center;
    line-height: 1;
  }
  .brand-name {
    display: block;
    font-size: 44px;
    letter-spacing: 0.5px;
  }
  .brand-sub {
    display: block;
    margin-top: 50px;
    font-size: 25px;
    letter-spacing: 0.5px;
  }
  .contact {
    position: absolute;
    left: 42px;
    top: 300px;
  }
  .person-name {
    color: var(--maroon);
    font-size: 26px;
    font-weight: 700;
    letter-spacing: 0.3px;
    line-height: 28px;
  }
  .person-role {
    color: var(--ink-soft);
    font-size: 16px;
    margin-left: 2px;
    line-height: 20px;
  }
  .phone {
    margin-top: 17px;
    color: var(--ink);
    font-size: 18px;
    font-weight: 700;
    line-height: 22px;
  }
  .address {
    margin-top: 19px;
    color: var(--ink-soft);
    font-size: 16px;
    line-height: 22px;
  }
  .services {
    position: absolute;
    left: 0;
    right: 0;
    top: 72px;
  }
  .divider {
    width: 148px;
    height: 1px;
    margin: 16px auto 16px;
    background: var(--rule);
    border: none;
  }
</style>
</head>
<body>
<div class="canvas">

  <section class="card card-front">
    <div class="brand">
      <span class="brand-name">CORVANE</span>
      <span class="brand-sub">CONSTRUCTION</span>
    </div>
    <div class="contact">
      <p class="person-name">DWAYNE HALSTER</p>
      <p class="person-role">Owner</p>
      <p class="phone">P: (580) 482-5096</p>
      <p class="address">4875 FM 309<br>Dunmore, OK 79412</p>
    </div>
  </section>

  <section class="card card-back">
    <div class="services">
      <p class="service-list">
        Roads, Substation Pads<br>
        Temporary Pads<br>
        Site Pads, | Land Leveling | Powerline<br>
        Row Cleaning | Land Clearing<br>
        Gates | Fencing,Construction Entrances<br>
        Excavation | Trenching<br>
        Underground Utilities<br>
        Directional Boring | Pile Driving.
      </p>
      <hr class="divider">
      <p class="about">
        We are a construction company that<br>
        uses heavy equipment<br>
        like bulldozers | motor graders/blades<br>
        dump trucks<br>
        backhoes | hydro axes &amp; skid loaders.
      </p>
      <hr class="divider">
      <p class="summary">
        We build roads, pads<br>
        install electric utility lines<br>
        waterlines underground.
      </p>
    </div>
  </section>

</div>
</body>
</html>
```